Veltrano.co - Polar Expeditions Specialists

We need a modern, visually striking business card for Veltrano.co, a company specialized in selling expedition cruises to the most remote regions on Earth, with a focus on the Arctic and Antarctica. The design should instantly communicate that the cardholder is an expert in polar travel. Use clean, premium aesthetics with cool tones like icy blue and white, possibly incorporating polar imagery (ice, glaciers, penguins, etc.)

Attached the logo

Contact Information for Business Card

Feels high-end and trustworthy.. Visually memorable — encourages people to keep it

Colors
0054AA
0677BA
7BADD7
CADEEF
E8F1F8

Requirements
Must have
• ice, glaciers, penguins, montains
Nice to have
• modern, transparente,

```html
<!DOCTYPE html>
<html lang="en">
<head>
<meta charset="utf-8">
<title>Veltrano.co Business Card</title>
<link rel="stylesheet" href="https://fonts.googleapis.com/css2?family=Poppins:wght@600;700&family=Lato:wght@400;700&display=swap">
<style>
  :root {
    --brand-blue: #3474b4;
    --card-white: #ffffff;
    --ink: #111111;
    --backdrop: #1f1f1f;
  }
  * { margin: 0; padding: 0; box-sizing: border-box; }
  html, body { width: 1200px; height: 1200px; overflow: hidden; background: var(--backdrop); }
  .canvas { position: relative; width: 1200px; height: 1200px; }
  .card { position: absolute; border-radius: 30px; overflow: hidden; }
  .card-front { left: 175px; top: 99px; width: 865px; height: 494px; background: var(--brand-blue); color: var(--card-white); }
  .card-back { left: 179px; top: 621px; width: 850px; height: 483px; background: var(--card-white); color: var(--ink); }

  .brand-mark { position: absolute; border-radius: 50%; }
  .card-front .brand-mark { left: 372px; top: 121px; width: 120px; height: 120px; background: var(--card-white); }
  .card-back .brand-mark { left: 604px; top: 49px; width: 100px; height: 100px; background: var(--brand-blue); }

  .brand-name { position: absolute; font-family: 'Poppins', sans-serif; font-weight: 700; white-space: nowrap; transform: translateX(-50%); line-height: 1; letter-spacing: -0.5px; }
  .brand-tagline { position: absolute; font-family: 'Poppins', sans-serif; font-weight: 600; white-space: nowrap; transform: translateX(-50%); line-height: 1; }
  .card-front .brand-name { left: 432px; top: 272px; font-size: 76px; }
  .card-front .brand-tagline { left: 432px; top: 351px; font-size: 23px; }
  .card-back .brand-name { left: 654px; top: 168px; font-size: 58px; color: var(--brand-blue); }
  .card-back .brand-tagline { left: 654px; top: 229px; font-size: 18px; color: var(--brand-blue); }

  .holder-name { position: absolute; left: 57px; top: 254px; font-family: 'Lato', sans-serif; font-weight: 700; font-size: 34px; color: var(--brand-blue); }
  .holder-role { position: absolute; left: 57px; top: 298px; font-family: 'Lato', sans-serif; font-size: 21px; }
  .divider { position: absolute; left: 64px; top: 341px; width: 733px; height: 2px; background: var(--ink); }

  .contact-list { position: absolute; left: 57px; top: 360px; list-style: none; font-family: 'Lato', sans-serif; font-size: 22px; }
  .contact-list li { display: flex; align-items: center; height: 33px; }
  .contact-list svg { width: 24px; height: 24px; margin-right: 18px; fill: var(--brand-blue); flex: none; }

  .address { position: absolute; right: 53px; top: 394px; text-align: right; font-family: 'Lato', sans-serif; font-size: 22px; line-height: 33px; }
</style>
</head>
<body>
<main class="canvas">
  <section class="card card-front">
    <div class="brand-mark" aria-hidden="true"></div>
    <div class="brand-name">Veltrano.co</div>
    <div class="brand-tagline">Polar Expeditions Specialists</div>
  </section>

  <section class="card card-back">
    <div class="brand-mark" aria-hidden="true"></div>
    <div class="brand-name">Veltrano.co</div>
    <div class="brand-tagline">Polar Expeditions Specialists</div>

    <h1 class="holder-name">Elias Marlowe</h1>
    <p class="holder-role">Owner</p>
    <div class="divider"></div>

    <ul class="contact-list">
      <li>
        <svg viewBox="0 0 24 24" aria-hidden="true"><path d="M6.6 10.8a15.1 15.1 0 0 0 6.6 6.6l2.2-2.2a1 1 0 0 1 1-.25 11.4 11.4 0 0 0 3.6.57 1 1 0 0 1 1 1V20a1 1 0 0 1-1 1A17 17 0 0 1 3 4a1 1 0 0 1 1-1h3.5a1 1 0 0 1 1 1c0 1.25.2 2.45.57 3.57a1 1 0 0 1-.25 1z"/></svg>
        055-987 210 634
      </li>
      <li>
        <svg viewBox="0 0 24 24" aria-hidden="true"><path d="M2 5h20v14H2z M3 6l9 7 9-7" fill="none"/><path d="M2 5h20v2l-10 7L2 7z"/><path d="M2 9l10 7 10-7v10H2z"/></svg>
        hello@veltrano.co
      </li>
      <li>
        <svg viewBox="0 0 24 24" aria-hidden="true"><path d="M12 2a10 10 0 1 0 0 20 10 10 0 0 0 0-20zm0 2a8 8 0 0 1 7.7 5.8H16l-1.5 2 1 3-2 2v2.5a8 8 0 0 1-8.7-9.7L7 11l2 1 1-2-2-2 1-2.5A8 8 0 0 1 12 4z"/></svg>
        www.veltrano.co
      </li>
    </ul>

    <address class="address" style="font-style: normal;">
      421, Address line goes here<br>
      45452, Country name
    </address>
  </section>
</main>
</body>
</html>
```